New Bicycle shop business card

Hi!
I'm looking for a business card for my new proffesional bike mechanics shop. This shop is only for fixing broken bikes and not selling bikes.
Peferbly a modern and sleek and modern design.
Colors: black, grey, red, white
Information:
Name: Rijwielwerkplaats Vanhoutte
Shop owner: Bart Vanhoutte & Marieke Segers
Website: www.rijwielwerkplaats-vanhoutte.be
Email: info@rijwielwerkplaats-vanhoutte.be
Phone number: +32471902368
Street adres: Kerkweg 46
9940 Bellebeke
Slogan/shop information: Herstellingen van alle merken.
Logo: see files.
Target Market(s)
People who seek a mechanic to fix or upgrade their bikes.
Contact Information for Business Card
Information:
Website: info@rijwielwerkplaats-vanhoutte.be
9940 Bellebeke
Logo: see files.

```html
<!DOCTYPE html>
<html lang="nl">
<head>
<meta charset="utf-8">
<title>Rijwielwerkplaats Vanhoutte – visitekaartje</title>
<link rel="stylesheet" href="https://fonts.googleapis.com/css2?family=Montserrat:wght@800&family=Open+Sans:wght@400;600;700&display=swap">
<style>
  :root {
    --bg: #2a2a2a;
    --red: #e8222b;
    --black: #1b1b1b;
    --grey: #8a8a8a;
    --grey-light: #a9a9a9;
    --white: #ffffff;
  }
  * { box-sizing: border-box; margin: 0; padding: 0; }
  html, body {
    width: 1200px; height: 900px; overflow: hidden;
    background: var(--bg);
    font-family: "Open Sans", Arial, sans-serif;
  }
  .canvas {
    width: 1200px; height: 900px;
    display: flex; flex-direction: column; align-items: center;
    justify-content: center; gap: 40px;
  }
  .card {
    position: relative;
    width: 700px; height: 400px;
    overflow: hidden;
  }
  /* Front */
  .card--front {
    background: var(--red);
    display: flex; flex-direction: column; align-items: center; justify-content: center;
  }
  .brand {
    display: flex; flex-direction: column; align-items: center; gap: 12px;
  }
  .brand__dot {
    width: 46px; height: 46px; border-radius: 50%;
  }
  .brand__name {
    font-family: "Montserrat", Arial, sans-serif;
    font-weight: 800;
    text-transform: uppercase;
    text-align: center;
    line-height: 1.15;
    letter-spacing: 2px;
  }
  .card--front .brand__dot { background: var(--black); }
  .card--front .brand__name { color: var(--black); font-size: 30px; }
  .slogan {
    position: absolute; bottom: 70px; left: 0; right: 0;
    text-align: center;
    color: var(--white);
    font-size: 15px; font-weight: 600;
  }
  /* Back */
  .card--back { background: var(--white); }
  .card__swoosh { position: absolute; inset: 0; }
  .card--back .brand {
    position: absolute; left: 20px; top: 150px; width: 270px;
  }
  .card--back .brand__dot { background: var(--red); width: 38px; height: 38px; }
  .card--back .brand__name { color: var(--black); font-size: 19px; letter-spacing: 1px; }
  .contact {
    position: absolute; left: 302px; top: 55px;
    border-left: 2px solid var(--red);
    padding: 6px 0 10px 24px;
  }
  .contact__label { color: var(--red); font-size: 15px; }
  .contact__owners { color: var(--grey); font-size: 19px; font-weight: 700; margin-bottom: 8px; }
  .contact__company { color: var(--red); font-size: 19px; font-weight: 700; }
  .contact__role { color: var(--black); font-size: 13px; font-weight: 600; margin-bottom: 10px; }
  .contact__list { list-style: none; }
  .contact__item {
    display: flex; align-items: center; gap: 10px;
    color: var(--grey); font-size: 14px; line-height: 1.55;
  }
  .contact__item svg { width: 13px; height: 13px; flex: none; }
  .address {
    position: absolute; left: 290px; top: 282px;
    color: var(--grey-light); font-size: 15px;
  }
</style>
</head>
<body>
<main class="canvas">

  <section class="card card--front" aria-label="Voorkant">
    <div class="brand">
      <span class="brand__dot"></span>
      <p class="brand__name">Rijwielwerkplaats<br>Vanhoutte</p>
    </div>
    <p class="slogan">Herstellingen van alle merken.</p>
  </section>

  <section class="card card--back" aria-label="Achterkant">
    <svg class="card__swoosh" viewBox="0 0 700 400" preserveAspectRatio="none" aria-hidden="true">
      <path d="M0,350 C300,345 520,300 700,225 L700,400 L0,400 Z" fill="var(--red)"/>
      <path d="M420,335 C560,310 640,262 700,212" fill="none" stroke="var(--black)" stroke-width="4"/>
      <path d="M470,324 C590,296 650,256 700,200" fill="none" stroke="var(--grey-light)" stroke-width="4"/>
    </svg>

    <div class="brand">
      <span class="brand__dot"></span>
      <p class="brand__name">Rijwielwerkplaats<br>Vanhoutte</p>
    </div>

    <div class="contact">
      <p class="contact__label">Shop owner:</p>
      <p class="contact__owners">Bart Vanhoutte &amp; Marieke Segers</p>
      <p class="contact__company">Rijwielwerkplaats Vanhoutte</p>
      <p class="contact__role">General Manager</p>
      <ul class="contact__list">
        <li class="contact__item">
          <svg viewBox="0 0 16 16"><path d="M3 1h3l1.5 4-2 1.2a9 9 0 0 0 4.3 4.3L11 8.5l4 1.5v3a2 2 0 0 1-2 2A12 12 0 0 1 1 3a2 2 0 0 1 2-2z" fill="var(--red)"/></svg>
          +32471902368
        </li>
        <li class="contact__item">
          <svg viewBox="0 0 16 16"><rect x="1" y="3" width="14" height="10" rx="1" fill="none" stroke="var(--red)" stroke-width="2"/><path d="M1 4l7 5 7-5" fill="none" stroke="var(--red)" stroke-width="2"/></svg>
          info@rijwielwerkplaats-vanhoutte.be
        </li>
        <li class="contact__item">
          <svg viewBox="0 0 16 16"><circle cx="8" cy="8" r="6.5" fill="none" stroke="var(--red)" stroke-width="2"/><path d="M1.5 8h13M8 1.5c-3 3.5-3 9.5 0 13M8 1.5c3 3.5 3 9.5 0 13" fill="none" stroke="var(--red)" stroke-width="1.4"/></svg>
          www.rijwielwerkplaats-vanhoutte.be
        </li>
      </ul>
    </div>

    <p class="address">Kerkweg 46 9940 Bellebeke</p>
  </section>

</main>
</body>
</html>
```